Card Design for my dog training business Brightpaw Obedience

Need a business card design for my dog training business with my new logo. Want the card to come off professional yet fun. Want it to be very eye catchy as well. I normally have these at vet clinics, pet stores, and groomers. so need it to look better than my competitors.
Target Market(s)
dog owners
Industry/Entity Type
Dog Training
Contact Information for Business Card
needs logo, my name and info
Font styles to use
Serif
Colors
0255a3
ffffff
ec1f27
000000
333333
fbfbfb
Requirements
Must have
- Brightpaw Obedience
- Felix Orland
- 415 903 2276
- info@brightpawobedience.example
- www.brightpawobedience.example

```html
<!DOCTYPE html>
<html lang="en">
<head>
<meta charset="utf-8">
<title>Brightpaw Obedience – Business Card</title>
<link rel="stylesheet" href="https://fonts.googleapis.com/css2?family=EB+Garamond:ital,wght@0,400;1,400&family=Lato:wght@400&display=swap">
<style>
  :root {
    --stage: #e9e6e1;
    --card: #f7f5f1;
    --card-edge: #ffffff;
    --blue: #0255a3;
    --ink: #000000;
    --text: #333333;
    --muted: #555555;
  }
  html, body {
    margin: 0;
    width: 1200px;
    height: 1047px;
    overflow: hidden;
    background: var(--stage);
  }
  .card {
    position: absolute;
    left: 126px;
    top: 265px;
    width: 948px;
    height: 516px;
    box-sizing: border-box;
    border-radius: 20px;
    background: var(--card);
    border: 2px solid var(--card-edge);
    box-shadow: 0 10px 30px rgba(0,0,0,0.12);
  }
  .holder-name {
    position: absolute;
    left: 50px;
    top: 50px;
    margin: 0;
    font-family: "EB Garamond", serif;
    font-weight: 400;
    font-size: 25px;
    letter-spacing: 0.5px;
    text-transform: uppercase;
    color: var(--blue);
  }
  .holder-role {
    position: absolute;
    left: 50px;
    top: 86px;
    margin: 0;
    font-family: "Lato", sans-serif;
    font-size: 21px;
    color: var(--text);
  }
  .address {
    position: absolute;
    left: 50px;
    top: 220px;
    margin: 0;
    font-family: "Lato", sans-serif;
    font-style: normal;
    font-size: 21px;
    line-height: 33px;
    color: var(--text);
    letter-spacing: 0.4px;
  }
  .contact-list {
    position: absolute;
    left: 50px;
    top: 370px;
    margin: 0;
    padding: 0;
    list-style: none;
    font-family: "Lato", sans-serif;
    font-size: 21px;
    line-height: 32px;
    color: var(--text);
    letter-spacing: 0.4px;
  }
  .contact-list li {
    display: flex;
    align-items: center;
    gap: 10px;
  }
  .contact-list svg {
    width: 14px;
    height: 14px;
    flex: none;
  }
  .brand {
    position: absolute;
    left: 470px;
    top: 130px;
    width: 410px;
    height: 290px;
    display: flex;
    flex-direction: column;
    align-items: center;
    justify-content: center;
    gap: 18px;
  }
  .brand-dot {
    width: 54px;
    height: 54px;
    border-radius: 50%;
    background: var(--ink);
  }
  .brand-name {
    margin: 0;
    font-family: "EB Garamond", serif;
    font-weight: 400;
    font-size: 46px;
    line-height: 1.05;
    text-align: center;
    color: var(--ink);
  }
  .tagline {
    position: absolute;
    left: 470px;
    width: 410px;
    top: 438px;
    margin: 0;
    text-align: center;
    font-family: "EB Garamond", serif;
    font-style: italic;
    font-size: 21px;
    color: var(--ink);
    white-space: nowrap;
  }
</style>
</head>
<body>
  <section class="card">
    <h1 class="holder-name">Felix Orland</h1>
    <p class="holder-role">Managing Director</p>

    <address class="address">
      1820 Larkin Avenue,<br>
      Riverton, NZ, 8024
    </address>

    <ul class="contact-list">
      <li>
        <svg viewBox="0 0 16 16" aria-hidden="true"><path d="M4 1.5l2.2 3-1.4 1.6c.8 1.9 2.2 3.4 4.1 4.4l1.6-1.4 3 2.2-1.2 2.6C7.3 13.6 2.3 8.6 1.4 2.8z" fill="var(--blue)"/></svg>
        415 903 2276
      </li>
      <li>
        <svg viewBox="0 0 16 16" aria-hidden="true"><rect x="1.5" y="3.5" width="13" height="9" rx="1" fill="none" stroke="var(--blue)" stroke-width="1.6"/><path d="M2 4.5l6 4.5 6-4.5" fill="none" stroke="var(--blue)" stroke-width="1.6"/></svg>
        info@brightpawobedience.example
      </li>
      <li>
        <svg viewBox="0 0 16 16" aria-hidden="true"><circle cx="8" cy="8" r="6.5" fill="none" stroke="var(--muted)" stroke-width="1.4"/><ellipse cx="8" cy="8" rx="2.8" ry="6.5" fill="none" stroke="var(--muted)" stroke-width="1.2"/><path d="M1.5 8h13" stroke="var(--muted)" stroke-width="1.2"/></svg>
        www.brightpawobedience.example
      </li>
    </ul>

    <div class="brand">
      <span class="brand-dot" aria-hidden="true"></span>
      <p class="brand-name">Brightpaw Obedience</p>
    </div>

    <p class="tagline">“Training dogs across Texas one dog at a time.”</p>
  </section>
</body>
</html>
```